Hall of Fame annnouncement graphic for social media

I need a social media Hall of Fame announcement designed in the styles of some of the examples I've posted. I have attached the two gentlemens head shots ... the names are Dale Brinton and Ray Pemberly

It is for the BRAXWOOD LINKS HONOR GALLERY also include 2026 Inductees ... I have also attached the logo... make the post in similar colors as the logo.

I need this tomorrow so I am going to pick a winner in the next 24 hours.

```html
<!DOCTYPE html>
<html lang="en">
<head>
<meta charset="utf-8">
<title>Braxwood Links Honor Gallery – 2026 Inductees</title>
<link rel="stylesheet" href="https://fonts.googleapis.com/css2?family=Archivo:wdth,wght@62..125,100..900&family=Pinyon+Script&display=swap">
<style>
  :root {
    --navy: #003180;
    --crimson: #b01c06;
    --paper: #f4f4f4;
    --mist: #d9d9d9;
    --white: #ffffff;
  }
  html, body {
    margin: 0;
    padding: 0;
    width: 1200px;
    height: 1200px;
    overflow: hidden;
    background: var(--paper);
  }
  .announcement {
    display: block;
    width: 1200px;
    height: 1200px;
  }
  .headline {
    font-family: "Archivo", sans-serif;
    font-weight: 900;
    font-stretch: 125%;
  }
  .headline--red { fill: var(--crimson); }
  .headline--navy { fill: var(--navy); }
  .subhead {
    font-family: "Pinyon Script", cursive;
    fill: var(--crimson);
  }
  .org-name {
    font-family: "Archivo", sans-serif;
    font-weight: 800;
    fill: var(--white);
    letter-spacing: 2px;
  }
  .inductee-name {
    font-family: "Archivo", sans-serif;
    font-weight: 900;
    font-stretch: 125%;
    fill: var(--white);
  }
</style>
</head>
<body>
<svg class="announcement" viewBox="0 0 1200 1200" xmlns="http://www.w3.org/2000/svg">
  <defs>
    <linearGradient id="venueTone" x1="0" y1="0" x2="1" y2="1">
      <stop offset="0" stop-color="#ffffff"/>
      <stop offset="0.45" stop-color="#eeeeee"/>
      <stop offset="1" stop-color="#d4d4d4"/>
    </linearGradient>
    <linearGradient id="portraitWarm" x1="0" y1="0" x2="0" y2="1">
      <stop offset="0" stop-color="#ece3dc"/>
      <stop offset="1" stop-color="#d9b9a3"/>
    </linearGradient>
    <linearGradient id="portraitSky" x1="0" y1="0" x2="0" y2="1">
      <stop offset="0" stop-color="#dcd8e6"/>
      <stop offset="1" stop-color="#eadde3"/>
    </linearGradient>
  </defs>

  <!-- backdrop -->
  <rect class="venue-backdrop" x="0" y="0" width="1200" height="1200" fill="url(#venueTone)"
        role="img" aria-label="Faded photo of the clubhouse entrance with trees"/>

  <!-- top banner -->
  <path class="top-banner" fill="var(--navy)"
        d="M0 0 H1200 V211 H738 C640 211 620 170 560 100 C520 50 500 21 440 21 H0 Z"/>
  <text class="org-name" x="900" y="82" font-size="34" text-anchor="middle">BRAXWOOD LINKS</text>
  <text class="org-name" x="900" y="128" font-size="34" text-anchor="middle">HONOR GALLERY</text>

  <!-- headline -->
  <text class="headline headline--red" x="79" y="140" font-size="124" textLength="380" lengthAdjust="spacingAndGlyphs">HALL</text>
  <text class="headline headline--red" x="79" y="245" font-size="124" textLength="188" lengthAdjust="spacingAndGlyphs">OF</text>
  <text class="headline headline--navy" x="79" y="482" font-size="306" textLength="1034" lengthAdjust="spacingAndGlyphs">FAME</text>

  <!-- subhead -->
  <text class="subhead" x="79" y="573" font-size="78">2026 Inductees</text>
  <rect class="subhead-rule" x="693" y="549" width="425" height="3" fill="var(--crimson)"/>

  <!-- portraits -->
  <rect x="85" y="625" width="429" height="458" fill="var(--white)"/>
  <rect class="portrait" x="89" y="629" width="421" height="450" fill="url(#portraitWarm)"
        role="img" aria-label="Headshot of Dale Brinton"/>
  <rect x="684" y="625" width="431" height="458" fill="var(--white)"/>
  <rect class="portrait" x="688" y="629" width="423" height="450" fill="url(#portraitSky)"
        role="img" aria-label="Headshot of Ray Pemberly"/>

  <!-- name band -->
  <rect class="name-band" x="0" y="1108" width="1200" height="53" fill="var(--crimson)"/>
  <text class="inductee-name" x="307" y="1149" font-size="40" text-anchor="middle">DALE BRINTON</text>
  <text class="inductee-name" x="900" y="1149" font-size="40" text-anchor="middle">RAY PEMBERLY</text>
</svg>
</body>
</html>
```